Sea Shipping Logistics Company

The business is a logistics company (sea shipping and other special logistics) and also sales of bulk building materials.
The Design should be minimalistic and give a feeling of power and connectivity.
When the client sees the card, they should get a feeling of confident. Dark overall color (background) and print should be red / white .See logo. The card will be printed on trifecta with the middle color being red.

One side should be the logo and a 5 / 6 word slogan
And other side name, contact (phone/email) and a QR Code.

Target Market(s)

Construction companies / Oil & Gas related companies

Industry/Entity Type

Ocean Bulk Cargo Solutions

Contact Information for Business Card

Name, Telephone number, Email address, Website URL, QR Code (see description)

Font styles to use
Sans Serif

Requirements
Must have
• No idea
Nice to have
• Minimalistic, but strong and powerful look and feel.

```html
<!DOCTYPE html>
<html lang="en">
<head>
<meta charset="UTF-8">
<title>Korda — Business Card</title>
<link href="https://fonts.googleapis.com/css2?family=Roboto:wght@400;500;700;900&family=Poppins:wght@400&display=swap" rel="stylesheet">
<style>
  :root {
    --bg: #231f1e;
    --card: #232325;
    --card-edge: #1a1a1b;
    --red: #d0021b;
    --white: #ffffff;
    --text: #e9e9ea;
    --emboss: #111112;
    --silver: #b9b9bb;
    --emboss-text: #8c8c8e;
  }
  * { margin: 0; padding: 0; box-sizing: border-box; }
  html, body { width: 1200px; height: 1200px; overflow: hidden; }
  body { background: var(--bg); font-family: "Roboto", sans-serif; position: relative; }

  .card {
    position: absolute;
    width: 594px;
    height: 348px;
    border-radius: 26px;
    background: var(--card);
    border: 1px solid var(--card-edge);
    overflow: hidden;
  }
  .card--front { left: 298px; top: 198px; }
  .card--back { left: 292px; top: 637px; }

  /* Front */
  .front-mark__square {
    position: absolute;
    left: 120px; top: 104px;
    width: 129px; height: 117px;
    border: 3px solid var(--emboss);
    background: #1d1d1f;
  }
  .front-mark__name {
    position: absolute;
    left: 256px; top: 112px;
    font-weight: 900;
    font-size: 80px;
    letter-spacing: -2px;
    color: var(--emboss-text);
    line-height: 1;
  }
  .front-tagline {
    position: absolute;
    left: 0; right: 0; top: 296px;
    text-align: center;
    font-family: "Poppins", sans-serif;
    font-size: 14.5px;
    letter-spacing: 1.2px;
    color: var(--text);
  }
  .front-tagline .sep { color: var(--red); margin: 0 14px; }

  /* Back */
  .back-mark__square {
    position: absolute;
    left: 90px; top: 71px;
    width: 115px; height: 102px;
    border: 3px solid var(--white);
  }
  .back-mark__name {
    position: absolute;
    left: 40px; width: 216px; top: 182px;
    font-weight: 900;
    font-size: 62px;
    letter-spacing: -2px;
    color: var(--white);
    line-height: 1;
    text-align: center;
  }
  .contact {
    position: absolute;
    left: 312px; top: 72px;
  }
  .contact__name {
    font-weight: 900;
    font-size: 28px;
    color: var(--red);
    line-height: 1;
    letter-spacing: 0.2px;
  }
  .contact__role {
    margin-top: 5px;
    font-size: 16px;
    color: var(--text);
  }
  .contact__list { list-style: none; margin-top: 38px; }
  .contact__item {
    display: flex; align-items: center; gap: 16px;
    font-size: 16px; color: var(--text);
    height: 22px;
  }
  .contact__item svg { width: 14px; height: 14px; flex: none; }
  .contact__address { margin-top: 4px; font-size: 16px; color: var(--text); }

  .back-band {
    position: absolute;
    right: 0; bottom: 0;
    width: 338px; height: 41px;
    background: var(--red);
    clip-path: polygon(20px 0, 100% 0, 100% 100%, 0 100%);
    display: flex; align-items: center;
    padding-left: 57px;
    font-size: 16px; color: var(--white);
  }
  .back-strip {
    position: absolute;
    left: 0; bottom: 0;
    width: 270px; height: 12px;
    background: var(--silver);
  }
</style>
</head>
<body>

<section class="card card--front">
  <div class="front-mark__square"></div>
  <div class="front-mark__name">KORDA</div>
  <p class="front-tagline">CARGO<span class="sep">|</span>TRANSPORT<span class="sep">|</span>SUPPLY</p>
</section>

<section class="card card--back">
  <div class="back-mark__square"></div>
  <div class="back-mark__name">KORDA</div>

  <div class="contact">
    <h1 class="contact__name">DANIEL BROOKS</h1>
    <p class="contact__role">Managing Director</p>
    <ul class="contact__list">
      <li class="contact__item">
        <svg viewBox="0 0 16 16" aria-hidden="true"><path fill="#d0021b" d="M2 5c0-2 2-3 6-3s6 1 6 3v1h-3V5H5v1H2zM4 7h8l2 7H2z"/><circle cx="8" cy="10.5" r="1.8" fill="#232325"/></svg>
        +597 810-2231
      </li>
      <li class="contact__item">
        <svg viewBox="0 0 16 16" aria-hidden="true"><rect x="1" y="3" width="14" height="10" fill="#d0021b"/><path d="M1 3l7 6 7-6" fill="none" stroke="#232325" stroke-width="1.4"/></svg>
        info@korda-cargo.com
      </li>
      <li class="contact__item">
        <svg viewBox="0 0 16 16" aria-hidden="true"><g fill="none" stroke="#d0021b" stroke-width="1.4"><circle cx="8" cy="8" r="6.3"/><ellipse cx="8" cy="8" rx="2.8" ry="6.3"/><path d="M1.7 8h12.6M3 4.5h10M3 11.5h10"/></g></svg>
        www.korda-cargo.com
      </li>
    </ul>
    <p class="contact__address">Kadeweg Noord, Suriname</p>
  </div>

  <div class="back-strip"></div>
  <div class="back-band">Ocean Bulk Cargo Solutions</div>
</section>

</body>
</html>
```